Business Card Design Project

We need a business card for a new technology services company. We develop software and implement software packages for our business customers and although we will begin with just one or two service offerings, our service offerings will expand over time. Our name comes from the an author, KL Barrow, and his "idea" was that opportunity should be based on ability and achievement, not on social status.

We would like to see a design that is standard in its size and shape, but stands apart in its dramatic color contrasts. The card should not use too many colors - the colors used in the background should highlight the brilliant blues of the logo (see attachment) to dramatic effect. The background should not be white.

If necessary, you can change the color of the words "KL Barrow", but not the word "Idea".

Card size should be U.S. standard 2 inches by 3.5 inches and provide for 1/8 inch bleed area on each side.

We need a design for both sides of the business card, one side communicating the company logo and contact information, the other side being purely graphical, incorporating the logo but no other information.

Contact Information Required:
Kate Brook
KateBrook@klbarrowvista.com
614-387-2259

Target Market(s)

Business executives

Industry/Entity Type

Software

Requirements
Must have
• It must have the full company logo on one side, and at least the graphic element of the logo on the other. Either that or the full logo on both.
Nice to have
• It would be nice to have a design that could work without needing two different textures. For example, it would be nice if the entire card could be shiny, not just parts of the card.

It would also be nice if texture is something we could add later.
Should not have
• The card should not use the color green.

```html
<!DOCTYPE html>
<html lang="en">
<head>
<meta charset="utf-8">
<title>KL Barrow Vista — Business Card</title>
<link rel="stylesheet" href="https://fonts.googleapis.com/css2?family=Cinzel:wght@400;500&family=Roboto:wght@300;400&display=swap">
<style>
  :root {
    --page-bg: #e9e6e2;
    --card-dark: #141414;
    --card-mid: #2f2f31;
    --brand-blue: #1ea0dd;
    --wordmark-grey: #a9a9ab;
    --text-light: #f2f2f2;
    --card-shadow: rgba(0, 0, 0, 0.35);
  }
  * { box-sizing: border-box; margin: 0; padding: 0; }
  html, body {
    width: 1200px;
    height: 750px;
    overflow: hidden;
    background: var(--page-bg);
  }
  .sheet {
    position: relative;
    width: 1200px;
    height: 750px;
  }
  .card {
    position: absolute;
    top: 220px;
    width: 540px;
    height: 309px;
    background: radial-gradient(ellipse at 55% 45%, var(--card-mid) 0%, var(--card-dark) 75%);
    box-shadow: 0 10px 24px var(--card-shadow);
    overflow: hidden;
  }
  .card--front { left: 40px; }
  .card--back  { left: 620px; }

  .wordmark {
    position: absolute;
    font-family: "Roboto", Arial, sans-serif;
    font-weight: 300;
    color: var(--wordmark-grey);
    white-space: nowrap;
  }
  .card--front .wordmark { right: 32px; top: 44px; font-size: 30px; }
  .card--back  .wordmark { left: 56px; top: 134px; font-size: 36px; }

  .mark-dot {
    position: absolute;
    border-radius: 50%;
    background: var(--brand-blue);
  }
  .card--front .mark-dot { left: 78px; top: 112px; width: 110px; height: 110px; }
  .card--back  .mark-dot { right: 52px; top: 104px; width: 100px; height: 100px; }

  .contact {
    position: absolute;
    left: 282px;
    top: 132px;
    color: var(--text-light);
  }
  .contact__name {
    font-family: "Cinzel", Georgia, serif;
    font-size: 19px;
    color: var(--brand-blue);
    text-decoration: underline;
    text-underline-offset: 3px;
    letter-spacing: 1px;
    margin-bottom: 22px;
  }
  .contact__line {
    display: flex;
    align-items: center;
    gap: 8px;
    font-family: "Roboto", Arial, sans-serif;
    font-size: 13px;
    margin-bottom: 9px;
  }
  .contact__icon { width: 11px; height: 11px; flex: none; }
</style>
</head>
<body>
  <main class="sheet">
    <section class="card card--front" aria-label="Card front">
      <div class="mark-dot" aria-hidden="true"></div>
      <div class="wordmark">KL Barrow Vista</div>
      <div class="contact">
        <p class="contact__name">Kate Brook</p>
        <p class="contact__line">
          <svg class="contact__icon" viewBox="0 0 12 12" aria-hidden="true">
            <path d="M2.5 1h2l1 3-1.5 1a6 6 0 0 0 3 3l1-1.5 3 1v2a1.5 1.5 0 0 1-1.5 1.5A9.5 9.5 0 0 1 1 2.5 1.5 1.5 0 0 1 2.5 1z" fill="#1ea0dd"/>
          </svg>
          <span>614-387-2259</span>
        </p>
        <p class="contact__line">
          <svg class="contact__icon" viewBox="0 0 12 12" aria-hidden="true">
            <rect x="1" y="2.5" width="10" height="7" rx="1" fill="#1ea0dd"/>
            <path d="M1.5 3l4.5 3.5L10.5 3" stroke="#141414" stroke-width="1" fill="none"/>
          </svg>
          <span>KateBrook@klbarrowvista.com</span>
        </p>
      </div>
    </section>

    <section class="card card--back" aria-label="Card back">
      <div class="wordmark">KL Barrow Vista</div>
      <div class="mark-dot" aria-hidden="true"></div>
    </section>
  </main>
</body>
</html>
```